I would like a minimalist clean and uncluttered website design.
Initially, I would like to see a front page only and would then like to build on the project front there.
DVQ logo file with no background is attached, can be grey scale if the designer wishes.
I would like the front page to speak about the company's ethos and goals and I will need to put a great deal of thought into this to ensure it has the desired impact with the content on the subsequent pages.
The paragraph below gives a bit of an idea as to what this will include.
"DVQ is a technology company providing approachable IT products and services to business:
With the overwhelming advancements in technology, businesses often find it difficult to determine what is available and what best suits their businesses specific needs.
We can assist business with their IT infrustucture, devices, software in procurement, installation, training, cost control as well as ongoing administration and support. We also keep our Clients informed of new technology and products which can benefit them"
Target Market(s)
Business, Health, Education, Professional Practices. Target age would be around 30 plus either male or female. Office administration level through Managing Directors. English speaking.

```html
<!DOCTYPE html>
<html lang="en">
<head>
<meta charset="utf-8">
<title>DVQ – Home</title>
<link rel="stylesheet" href="https://fonts.googleapis.com/css2?family=Open+Sans:ital,wght@0,300;0,400;0,600;1,300&family=Questrial&display=swap">
<style>
:root{
  --header-bg:#2f3136;
  --header-line:#3a4a86;
  --hero-dark:#34373d;
  --hero-mid:#4a4d54;
  --green:#8db33a;
  --navy:#2f3d6f;
  --nav-text:#a7a9ad;
  --text-dark:#444;
  --text-mid:#555;
  --text-light:#9a9a9a;
  --rule:#e2e2e2;
  --page-bg:#f3f3f3;
  --footer-bg:#efefef;
  --social:#555;
}
*{margin:0;padding:0;box-sizing:border-box}
html,body{width:1189px;height:1200px;overflow:hidden}
body{position:relative;background:var(--page-bg);font-family:"Open Sans",sans-serif;color:var(--text-mid)}
.site-header{position:absolute;left:0;top:0;width:1189px;height:82px;background:var(--header-bg);border-top:3px solid var(--header-line);border-bottom:1px solid #24262a}
.brand{position:absolute;left:132px;top:24px;display:flex;align-items:center;gap:8px}
.brand-mark{width:14px;height:14px;background:var(--green)}
.brand-name{font-weight:400;font-size:19px;color:#c9cbce;letter-spacing:.3px}
.main-nav a{position:absolute;top:30px;font-size:17px;color:var(--nav-text);text-decoration:none;line-height:20px}
.main-nav a.is-current{color:var(--green)}
.login{position:absolute;left:933px;top:30px;width:56px;height:19px;background:var(--green);border-radius:3px;color:#2f3136;font-size:13.5px;line-height:19px;text-align:center}
.signup{position:absolute;left:1004px;top:30px;font-size:13.5px;color:#fff;line-height:19px}
.hero{position:absolute;left:0;top:82px;width:1189px;height:151px;background:linear-gradient(90deg,var(--hero-dark) 0%,var(--hero-mid) 45%,#3e4148 100%)}
.hero-tagline{position:absolute;right:327px;top:52px;text-align:right;font-style:italic;font-weight:300;font-size:15px;line-height:22px;color:#d4d5d7}
.hero-title{position:absolute;left:876px;top:50px;font-weight:400;font-size:47px;line-height:50px;color:var(--green);letter-spacing:-1.5px}
.content-card{position:absolute;left:127px;top:233px;width:937px;height:863px;background:#fff;border-left:1px solid var(--rule);border-right:1px solid var(--rule)}
.sidebar{position:absolute;left:0;top:0;width:242px;height:863px;background:linear-gradient(180deg,#fafafa,#fff);border-right:1px solid var(--rule)}
.sidebar-title{position:absolute;left:32px;top:44px;font-family:"Questrial",sans-serif;font-weight:400;font-size:18px;color:var(--navy)}
.service-list{position:absolute;left:31px;top:86px;width:211px;list-style:none;border-top:1px solid var(--rule)}
.service-list li{position:relative;height:36.5px;border-bottom:1px solid var(--rule);font-family:"Questrial",sans-serif;font-size:14.5px;color:var(--text-dark);line-height:36px;padding-left:48px}
.service-list svg{position:absolute;left:16px;top:11px;width:14px;height:14px}
.main{position:absolute;left:271px;top:0;width:640px}
.section-title{position:absolute;font-family:"Questrial",sans-serif;font-weight:400;font-size:18px;color:var(--green);line-height:22px}
.lead{position:absolute;font-size:15.5px;color:var(--text-dark);line-height:20px}
.body-text{position:absolute;width:625px;font-size:12.6px;font-weight:300;color:var(--text-light);line-height:17.8px}
.check-list{position:absolute;list-style:none}
.check-list li{position:relative;height:21.5px;padding-left:27px;font-size:12.5px;font-weight:600;color:var(--text-mid);line-height:16px}
.check-list svg{position:absolute;left:1px;top:2px;width:12px;height:12px}
.site-footer{position:absolute;left:0;top:1096px;width:1189px;height:104px;background:var(--footer-bg);border-top:1px solid var(--rule)}
.footer-links{position:absolute;left:128px;top:42px;font-size:11.5px;color:#666;line-height:16px}
.footer-links .sep{margin:0 6px;color:#888}
.social{position:absolute;left:976px;top:41px;display:flex;gap:5px}
.social span{width:18px;height:18px;border-radius:50%;background:var(--social)}
</style>
</head>
<body>
<header class="site-header">
  <div class="brand"><span class="brand-mark"></span><span class="brand-name">Dovequay</span></div>
  <nav class="main-nav">
    <a style="left:419px" class="is-current">Home</a>
    <a style="left:506px">Services</a>
    <a style="left:609px">Project</a>
    <a style="left:703px">Articles</a>
    <a style="left:800px">Contact</a>
  </nav>
  <span class="login">Log in</span>
  <span class="signup">sign up</span>
</header>

<section class="hero" role="img" aria-label="Dim photographic banner of an office workspace">
  <p class="hero-tagline">DVQ is a technology company providing<br>approachable IT products and services to business.</p>
  <h1 class="hero-title">WELCOME</h1>
</section>

<div class="content-card">
  <aside class="sidebar">
    <h2 class="sidebar-title">SERVICES</h2>
    <ul class="service-list">
      <li><svg viewBox="0 0 14 14" fill="none" stroke="#b5b5b5"><rect x="1" y="2" width="12" height="8"/><path d="M5 13h4M7 10v3"/></svg>IT infrustucture</li>
      <li><svg viewBox="0 0 14 14" fill="none" stroke="#b5b5b5"><rect x="3.5" y="1" width="7" height="12" rx="1"/></svg>Devices</li>
      <li><svg viewBox="0 0 14 14" fill="none" stroke="#b5b5b5"><circle cx="7" cy="7" r="6"/><circle cx="7" cy="7" r="2" fill="#b5b5b5"/></svg>Software</li>
      <li><svg viewBox="0 0 14 14" fill="none" stroke="#b5b5b5"><path d="M3 1h8M3 13h8M4 1c0 4 6 4 6 6s-6 2-6 6M10 1c0 4-6 4-6 6s6 2 6 6"/></svg>Installation</li>
      <li><svg viewBox="0 0 14 14" fill="#b5b5b5"><circle cx="5" cy="4" r="2.5"/><circle cx="10" cy="5" r="2"/><path d="M0 12c0-4 10-4 10 0zM9 9c3-1 5 1 5 3h-4z"/></svg>Training</li>
      <li><svg viewBox="0 0 14 14" fill="#b5b5b5"><path d="M5 1h4l-1 3h-2z"/><ellipse cx="7" cy="9.5" rx="5" ry="4.5"/></svg>Cost control</li>
    </ul>
  </aside>

  <main class="main">
    <h3 class="section-title" style="left:27px;top:62px">Our Ethos</h3>
    <p class="lead" style="left:28px;top:88px">Approachable IT products and services for every business.</p>
    <p class="body-text" style="left:28px;top:125px">With the overwhelming advancements in technology, businesses often find it difficult to determine what is available and what best suits their business's specific needs. We believe technology should be simple to understand, sensible to buy and easy to live with. That is why we listen first, explain clearly and recommend only what truly serves your people, your budget and the way you already work.</p>

    <p class="lead" style="left:27px;top:260px">How we help your business day to day.</p>
    <p class="body-text" style="left:27px;top:296px">We can assist business with their IT infrustucture, devices and software, from procurement through installation, training and cost control, as well as ongoing administration and support, so you can stay focused on running your organisation.</p>

    <ul class="check-list" style="left:28px;top:385px">
      <li><svg viewBox="0 0 12 12" fill="none" stroke="#bbb"><rect x=".5" y=".5" width="11" height="11"/><path d="M3 6l2 2 5-6"/></svg>IT infrastructure planning</li>
      <li><svg viewBox="0 0 12 12" fill="none" stroke="#bbb"><rect x=".5" y=".5" width="11" height="11"/><path d="M3 6l2 2 5-6"/></svg>Devices and hardware</li>
      <li><svg viewBox="0 0 12 12" fill="none" stroke="#bbb"><rect x=".5" y=".5" width="11" height="11"/><path d="M3 6l2 2 5-6"/></svg>Software procurement</li>
      <li><svg viewBox="0 0 12 12" fill="none" stroke="#bbb"><rect x=".5" y=".5" width="11" height="11"/><path d="M3 6l2 2 5-6"/></svg>Installation and setup</li>
      <li><svg viewBox="0 0 12 12" fill="none" stroke="#bbb"><rect x=".5" y=".5" width="11" height="11"/><path d="M3 6l2 2 5-6"/></svg>Staff training</li>
      <li><svg viewBox="0 0 12 12" fill="none" stroke="#bbb"><rect x=".5" y=".5" width="11" height="11"/><path d="M3 6l2 2 5-6"/></svg>Cost control</li>
      <li><svg viewBox="0 0 12 12" fill="none" stroke="#bbb"><rect x=".5" y=".5" width="11" height="11"/><path d="M3 6l2 2 5-6"/></svg>Ongoing administration and support</li>
    </ul>
    <ul class="check-list" style="left:297px;top:385px">
      <li><svg viewBox="0 0 12 12" fill="none" stroke="#bbb"><rect x=".5" y=".5" width="11" height="11"/><path d="M3 6l2 2 5-6"/></svg>Business</li>
      <li><svg viewBox="0 0 12 12" fill="none" stroke="#bbb"><rect x=".5" y=".5" width="11" height="11"/><path d="M3 6l2 2 5-6"/></svg>Health</li>
      <li><svg viewBox="0 0 12 12" fill="none" stroke="#bbb"><rect x=".5" y=".5" width="11" height="11"/><path d="M3 6l2 2 5-6"/></svg>Education</li>
      <li><svg viewBox="0 0 12 12" fill="none" stroke="#bbb"><rect x=".5" y=".5" width="11" height="11"/><path d="M3 6l2 2 5-6"/></svg>Professional practices</li>
      <li><svg viewBox="0 0 12 12" fill="none" stroke="#bbb"><rect x=".5" y=".5" width="11" height="11"/><path d="M3 6l2 2 5-6"/></svg>Office administration teams</li>
      <li><svg viewBox="0 0 12 12" fill="none" stroke="#bbb"><rect x=".5" y=".5" width="11" height="11"/><path d="M3 6l2 2 5-6"/></svg>Managing directors</li>
    </ul>

    <h3 class="section-title" style="left:28px;top:590px">Our Goals</h3>
    <p class="lead" style="left:28px;top:616px">Keeping our Clients informed, confident and ahead.</p>
    <p class="body-text" style="left:28px;top:653px">We also keep our Clients informed of new technology and products which can benefit them. Our goal is to be the trusted partner you call first: a team that removes the guesswork from IT decisions, delivers lasting value for every dollar spent, and grows alongside your business as its needs change over the years ahead.</p>
  </main>
</div>

<footer class="site-footer">
  <p class="footer-links">Home<span class="sep">|</span>Services<span class="sep">|</span>Project<span class="sep">|</span>Articles<span class="sep">|</span>Contact<span class="sep">|</span>Copyright © 2013 Dovequay.</p>
  <div class="social" aria-label="Social links"><span></span><span></span><span></span><span></span></div>
</footer>
</body>
</html>
```